we need a pizza box design for the 12 inch pizza consist of the 3 color no specific color for the logo or for the design the box is the same shape of the velmora pizza box attached i need to write few things like : hot s& delicious and Fall in Love with Pizza
adress on the box N17 Ebelu tanko way harlow bend ostavia
tel.: 0803 71 219 86
i might add the pizza name with check box
for example
margarita O
Vandos pizza
Tuka Pizza
seafood Pizza
other --------------
with check box next to it i have 8 type of pizza

Target Market(s)

its a pizza box people are buying it anyway

Industry/Entity Type

Restaurant

Font styles to use
Serif
Decorative
Script

Colors
abd037
eaf2ce
9ccb3b

Requirements
Must have
• simple and elegant
• with real carton color not white
Nice to have
• new creative idea
Should not have
• no pork or bacon

```html
<!DOCTYPE html>
<html lang="en">
<head>
<meta charset="utf-8">
<title>Korvale Pizzeria – Pizza Box</title>
<link rel="stylesheet" href="https://fonts.googleapis.com/css2?family=Cormorant+Garamond:wght@600&family=Rye&family=Stardos+Stencil:wght@700&family=Old+Standard+TT:wght@700&display=swap">
<style>
  :root {
    --paper: #ffffff;
    --kraft: #c6a57c;
    --kraft-edge: #b08c62;
    --kraft-side: #bb996f;
    --brown: #7b2816;
    --red: #c3211b;
    --cream: #e3cba3;
  }
  html, body {
    margin: 0;
    width: 1200px;
    height: 896px;
    overflow: hidden;
    background: var(--paper);
  }
  .canvas {
    position: relative;
    width: 1200px;
    height: 896px;
  }
  .box-dieline {
    position: absolute;
    left: 60px;
    top: 70px;
    width: 760px;
    height: 760px;
  }
  .brand-name {
    position: absolute;
    left: 850px;
    top: 110px;
    width: 300px;
    margin: 0;
    text-align: center;
    font-family: "Cormorant Garamond", serif;
    font-weight: 600;
    font-size: 44px;
    line-height: 1.1;
    color: var(--brown);
  }
  .lid-stencil { font-family: "Stardos Stencil", serif; font-weight: 700; }
  .lid-slab { font-family: "Rye", serif; }
  .side-text { font-family: "Old Standard TT", serif; font-weight: 700; }
  .label-text { font-family: "Cormorant Garamond", serif; font-weight: 600; }
</style>
</head>
<body>
<main class="canvas">

  <svg class="box-dieline" viewBox="0 0 760 760" xmlns="http://www.w3.org/2000/svg" aria-label="Pizza box lid with front and side panels">
    <defs>
      <clipPath id="lid-shape">
        <polygon points="60,0 580,0 640,60 640,580 580,640 60,640 0,580 0,60"/>
      </clipPath>
    </defs>

    <g class="lid">
      <polygon points="60,0 580,0 640,60 640,580 580,640 60,640 0,580 0,60" fill="var(--kraft)" stroke="var(--kraft-edge)" stroke-width="2"/>

      <g clip-path="url(#lid-shape)">
        <polygon class="pizza-wedge" points="180,640 640,640 640,220 390,320" fill="var(--brown)"/>
        <text class="lid-stencil" transform="translate(460,550) rotate(-40)" fill="var(--cream)" font-size="96" text-anchor="middle">PIZZA</text>
      </g>

      <g class="lid-label">
        <rect x="300" y="40" width="180" height="120" fill="var(--brown)"/>
        <text class="label-text" x="390" y="110" fill="var(--cream)" font-size="30" text-anchor="middle">Korvale</text>
        <rect x="300" y="166" width="180" height="34" fill="var(--brown)"/>
        <text class="label-text" x="390" y="190" fill="var(--cream)" font-size="18" letter-spacing="4" text-anchor="middle">MARGARITA</text>
      </g>

      <g class="lid-slab" transform="translate(40,330) rotate(-12)">
        <text x="0" y="0" fill="var(--red)" font-size="44">HOT <tspan fill="var(--brown)">AND</tspan></text>
        <text x="0" y="50" fill="var(--brown)" font-size="40">DELICIOUS</text>
      </g>
    </g>

    <g class="front-panel">
      <rect x="40" y="650" width="560" height="100" fill="var(--kraft-side)" stroke="var(--kraft-edge)" stroke-width="2"/>
      <text class="side-text" x="60" y="685" fill="var(--brown)" font-size="20">N17 Ebelu tanko way harlow bend ostavia</text>
      <text class="side-text" x="60" y="730" fill="var(--brown)" font-size="38">0803 71 <tspan fill="var(--red)">219</tspan> 86</text>
    </g>

    <g class="side-panel">
      <rect x="650" y="40" width="100" height="560" fill="var(--kraft-side)" stroke="var(--kraft-edge)" stroke-width="2"/>
      <text class="side-text" transform="translate(712,580) rotate(-90)" fill="var(--brown)" font-size="36">FALL IN <tspan fill="var(--red)">LOVE</tspan> WITH PIZZA</text>
    </g>
  </svg>

  <p class="brand-name">Korvale Pizzeria</p>

</main>
</body>
</html>
```